Tandem Pocket Apps Needs banners for webpage

We need a top banner. We are a mobile app developer for the Hospitality Industry. We are developing a Loyalty Program with the trade name TandemPerks. The banner will be used on our loyalty page inside our website.Please see www.tandempocketapps.example to understand our theme. The banner should be 1700 X 470.

Please see the attached banner. This is from a competitor website.Please use it as a model and make changes...... make it unique to TandemPocket. I need to convey the same message as this banner. Same statistics. Same setting (restaurant).

I have added a purchased vector file for the restaurant setting. I noticed many are struggling and using stock art which I don't like.Work with the background color. Make it more playful--pastels--less formal. Be creative!

Do not wait till that last day of the contest to submit. I might take the first design I like and proceed. The sooner you post a design, the better direction I can give you.
Updates

Project Deadline Extended
Reason: Not getting any designs I can work with yet. Please give me ideas.

All, Please re-read the brief. I have changed the banner project. It will be much easier but I need it quickly.

Now that I have made this banner much easier, I would like to wrap this contest up. Don't wait till the last day to post designs. The first design I like I will go with and close the project. Be creative, colorful, imaginative! Good luck. Marcus Hennet Tandem Pocket Apps, LLC mhennet@

All. See the vector file that I just purchased for the background image. Can you try different background colors. I still need the other content showing the percentages of loyalty. I do not want the rocket ship!

All, I have updated the brief. I have included a vector file that has a perfect restaurant scene. Please be creative and work with colors in this scene. Also be creative with the information in the circles showing the metrics of loyalty. Do not use the Rocket. If you find another idea to replace the rocket, that's fine. Or, just leave it off. Please make this banner unique!

Target Market(s)

Hospitality Industry.

Industry/Entity Type

Restaurant

Requirements
Must have
• Banner should be beautiful.. Image of diners at restaurant along with the statistics and message "Boost Sales".
Nice to have
• Our banner should convey the same message as the attached but we must re-design because the attached banner belongs to another company.
Should not have
• Do not re-use any of the images in the attached banner. This is from my competitor. Do not use a rocket for "Boost Sales" image.

```html
<!DOCTYPE html>
<html lang="en">
<head>
<meta charset="utf-8">
<title>Boost Sales – Loyal Guest vs. Average Guest</title>
<link rel="stylesheet" href="https://fonts.googleapis.com/css2?family=Arvo:wght@400;700&family=Didact+Gothic&family=Playball&display=swap">
<style>
  :root {
    --apricot: #f0b862;
    --apricot-deep: #c98c3e;
    --caramel: #bf8f4e;
    --cream: #fbf6ef;
    --rose-rim: #c97470;
    --ink: #1e1a18;
    --signal-red: #d8141e;
    --white: #ffffff;
  }
  html, body {
    margin: 0;
    padding: 0;
    width: 1200px;
    height: 331px;
    overflow: hidden;
    background: var(--apricot);
  }
  .banner {
    position: relative;
    width: 1200px;
    height: 331px;
    overflow: hidden;
  }
  .dining-scene {
    position: absolute;
    inset: 0;
    background:
      radial-gradient(ellipse 55% 70% at 50% 62%, #b07a34 0%, rgba(176,122,52,0.35) 45%, rgba(240,184,98,0) 75%),
      linear-gradient(180deg, var(--apricot) 0%, #e9ad57 100%);
  }
  .title-plate {
    position: absolute;
    left: 463px;
    top: 0;
    width: 274px;
    height: 90px;
    background: var(--caramel);
    color: var(--white);
    text-align: center;
  }
  .title-plate h1 {
    margin: 12px 0 0;
    font-family: "Arvo", serif;
    font-weight: 400;
    font-size: 36px;
    line-height: 42px;
    letter-spacing: 0.5px;
  }
  .title-plate p {
    margin: 6px 0 0;
    font-family: "Didact Gothic", sans-serif;
    font-size: 14px;
    letter-spacing: 0.3px;
  }
  .stat-badge {
    position: absolute;
    width: 170px;
    height: 170px;
    border-radius: 50%;
    background: var(--cream);
    border: 4px solid var(--rose-rim);
    color: var(--ink);
    font-family: "Playball", cursive;
    text-align: center;
  }
  .stat-badge .lead,
  .stat-badge .tail {
    position: absolute;
    left: 0;
    right: 0;
    font-size: 12.5px;
    line-height: 16px;
  }
  .stat-badge .lead { top: 36px; }
  .stat-badge .tail { top: 112px; }
  .stat-badge .figure {
    position: absolute;
    left: 0;
    right: 0;
    top: 54px;
    font-size: 44px;
    line-height: 56px;
    color: var(--signal-red);
  }
  .badge-visits { left: 241px; top: 115px; }
  .badge-spend  { left: 515px; top: 115px; }
  .badge-worth  { left: 779px; top: 112px; }
  .badge-worth .lead { top: 34px; }
  .badge-worth .tail { top: 118px; }
  .guest-icons {
    position: absolute;
    left: 38px;
    top: 62px;
    width: 94px;
    height: 52px;
  }
  .page-tag {
    position: absolute;
    right: 28px;
    top: 300px;
    font-family: "Didact Gothic", sans-serif;
    font-size: 11px;
    color: var(--white);
  }
</style>
</head>
<body>
  <main class="banner">
    <div class="dining-scene" role="img" aria-label="Silhouetted diners and a waiter in a warm apricot restaurant scene"></div>

    <header class="title-plate">
      <h1>Boost Sales</h1>
      <p>Loyal Guest vs. Average Guest</p>
    </header>

    <section class="stat-badge badge-visits">
      <span class="lead">Loyal Guests Visit About</span>
      <span class="figure">32%</span>
      <span class="tail">More Than Average Guests</span>
    </section>

    <section class="stat-badge badge-spend">
      <span class="lead">Loyal Guests Spend About</span>
      <span class="figure">22%</span>
      <span class="tail">More Than Average Guests</span>
    </section>

    <section class="stat-badge badge-worth">
      <span class="lead">1 Loyal Guest =</span>
      <svg class="guest-icons" viewBox="0 0 94 52" aria-hidden="true">
        <g fill="var(--signal-red)">
          <circle cx="17" cy="10" r="9"/>
          <path d="M0 52 V34 a17 14 0 0 1 34 0 V52 Z"/>
          <circle cx="61" cy="7" r="4.5"/>
          <path d="M53 28 V20 a8 7 0 0 1 16 0 V28 Z"/>
          <circle cx="84" cy="7" r="4.5"/>
          <path d="M76 28 V20 a8 7 0 0 1 16 0 V28 Z"/>
          <circle cx="72" cy="31" r="4.5"/>
          <path d="M64 52 V44 a8 7 0 0 1 16 0 V52 Z"/>
        </g>
        <g fill="var(--cream)">
          <path d="M15.5 26 h3 l1.5 18 -3 4 -3 -4 Z"/>
          <path d="M60.3 15 h1.4 l0.8 8 -1.5 2 -1.5 -2 Z"/>
          <path d="M83.3 15 h1.4 l0.8 8 -1.5 2 -1.5 -2 Z"/>
          <path d="M71.3 39 h1.4 l0.8 8 -1.5 2 -1.5 -2 Z"/>
        </g>
      </svg>
      <span class="tail">10 Average Guests</span>
    </section>

    <span class="page-tag">C6</span>
  </main>
</body>
</html>
```